Torvane Email Signature Banners – Fabrication Capability Series

www.Torvane.com.au is an Australian engineering and fabrication company specialising in fabrication and welding of :
steel piping spools,
skids and frames,
small volume process steel tanks
and general steel fabrication
We require four distinct banner designs for use in Microsoft Lintaro email signatures. Each banner will highlight a specific capability while maintaining a consistent brand identity.
Deliverables
Four banners total:
Piping Spools Fabrication – focus on precision welding and stainless steel pipework
Skid & Frames Fabrication – highlight skid systems and structural frames
Small Steel Tanks Fabrication – show fabricated tanks and workshop craftsmanship
General Fabrication Solutions – broad steel fabrication theme for company-wide use
Dimensions: 600–700 px wide × 100 px high
Format: PNG (preferred), small file size prefered
Resolution: 72 dpi
Background: non-transparent, industrial or workshop setting
Text examples:
1. Piping Spools Fabrication
Option A: “Expert Fabrication Solutions for Process Piping”
Option B: “Precision Welding for Complex Systems”
Option C: “Delivering Quality in Every Spool”
Option D: “Engineered for Flow, Built for Strength”
2. Skid & Frames Fabrication
Option A: “Custom Engineered Modular Systems”
Option B: “Built Strong. Designed Smart.”
Option C: “Reliable Frames for Industrial Performance”
Option D: “Modular Fabrication for Seamless Integration”
3. Small Steel Tanks Fabrication
Option A: “Precision Built for Your Needs”
Option B: “Compact Strength. Proven Durability.”
Option C: “Fabricated for Performance and Longevity”
Option D: “Small Tanks. Big Reliability.”
4. General Fabrication Solutions
Option A: “Quality Craftsmanship, Proven Results”
Option B: “Your Partner in Precision Fabrication”
Option C: “Engineering Excellence in Every Weld”
Option D: “Australian Fabrication. Global Standards.”
Style Direction
Clean, professional, and engineering‑focused
Use Torvane brand colours
Blend photo realism with vector clarity (no heavy gradients)
Include subtle industrial textures or workshop imagery
Typography: bold sans‑serif, legible at small scale
Usage Context
These banners will appear at the bottom of staff email signatures via Lintaro Email Signature Tool for Microsoft 365, so clarity and fast loading are essential. No Logo is required in the banners.
Reference
Existing Torvane signature is attached. Colour palette to match the signature style and logo.
Target Market(s)
Engineering and construction companies,
Industry/Entity Type
Engineering fabrication design
Look and feel

```html
<!DOCTYPE html>
<html lang="en">
<head>
<meta charset="utf-8">
<title>Piping Spools Fabrication Banner</title>
<link rel="stylesheet" href="https://fonts.googleapis.com/css2?family=Montserrat:wght@600;800&display=swap">
<style>
  :root {
    --brand-deep: #0b3a8c;
    --brand-mid: #1557bf;
    --brand-bright: #2a78e0;
    --accent-line: #4fb3ff;
    --band-light: rgba(120, 180, 255, 0.22);
    --photo-steel: #5f6e80;
    --photo-sky: #9fb3c8;
    --photo-shadow: #3b4756;
    --text-light: #ffffff;
  }
  html, body {
    margin: 0;
    padding: 0;
    width: 1200px;
    height: 200px;
    overflow: hidden;
    background: #ffffff;
  }
  .banner {
    position: relative;
    width: 1200px;
    height: 200px;
    overflow: hidden;
    background: linear-gradient(100deg, var(--brand-deep) 0%, var(--brand-mid) 55%, var(--brand-bright) 100%);
    font-family: "Montserrat", Arial, sans-serif;
    color: var(--text-light);
  }
  .banner__shapes {
    position: absolute;
    inset: 0;
  }
  .banner__headline {
    position: absolute;
    left: 28px;
    top: 3px;
    margin: 0;
    font-weight: 800;
    font-size: 38px;
    line-height: 52px;
    letter-spacing: 0.3px;
    text-transform: uppercase;
    white-space: nowrap;
  }
  .banner__service {
    position: absolute;
    left: 84px;
    top: 127px;
    margin: 0;
    font-weight: 600;
    font-size: 26px;
    line-height: 30px;
    white-space: nowrap;
  }
</style>
</head>
<body>
  <div class="banner">
    <svg class="banner__shapes" width="1200" height="200" viewBox="0 0 1200 200">
      <defs>
        <linearGradient id="workshopTone" x1="0" y1="0" x2="1" y2="1">
          <stop offset="0" stop-color="var(--photo-sky)"/>
          <stop offset="0.5" stop-color="var(--photo-steel)"/>
          <stop offset="1" stop-color="var(--photo-shadow)"/>
        </linearGradient>
      </defs>
      <polygon class="band-light" points="0,200 0,122 112,92 600,200" fill="var(--band-light)"/>
      <polyline class="accent-line" points="0,122 112,92 360,200" fill="none" stroke="var(--accent-line)" stroke-width="3"/>
      <polygon class="workshop-photo" role="img"
        aria-label="Photo: workers in hard hats and hi-vis guiding a large steel pipe spool lifted by crane chains"
        points="800,0 1200,0 1200,200 690,200" fill="url(#workshopTone)"/>
      <polyline class="accent-line" points="800,0 690,200" fill="none" stroke="var(--accent-line)" stroke-width="3"/>
    </svg>
    <h1 class="banner__headline">Expert Fabrication Solutions<br>for Process Piping</h1>
    <p class="banner__service">Piping Spools Fabrication</p>
  </div>
</body>
</html>
```